Business cards to launch an education platform

Hi,
I am looking at having new business cards designed.
I am a startup, developing a web platform for schools and university, the education world. It's an online assessment system.
I would like a card that looks classy, and that is using the colors and the font of my logo.

I have attached:
1) my logo
2) A business card that I have designed quickly so you can have all the information required in the card, but I really don't like it.
3) The font that I am using (Lato Regular) to design my web platform
4) Some screenshots of my web platform so you can have a look at the style that I have.

Target Market(s)

Major market: Education system: Schools and university
Minor markets: Business in general

Industry/Entity Type

Business

Contact Information for Business Card

Clara Fenwick
Director

M: 0437 518 902
E: clara.fenwick@amberLoomSystems.com.au

Requirements
Must have
• The colors of my logo

```html
<!DOCTYPE html>
<html lang="en">
<head>
<meta charset="utf-8">
<title>Amber Loom Systems — Business Cards</title>
<link rel="stylesheet" href="https://fonts.googleapis.com/css2?family=Lato:wght@300;400;700&display=swap">
<style>
  :root {
    --backdrop: #9a9b9d;
    --card-paper: #eeeff1;
    --navy: #0b3664;
    --navy-deep: #08305a;
    --sky: #2a9fd6;
    --ink: #3b3e44;
    --pale-text: #e3e9f0;
  }
  * { box-sizing: border-box; margin: 0; padding: 0; }
  html, body {
    width: 1105px;
    height: 1200px;
    overflow: hidden;
    background: var(--backdrop);
    font-family: "Lato", Arial, sans-serif;
  }
  .canvas { position: relative; width: 1105px; height: 1200px; }

  .card {
    position: absolute;
    left: 182px;
    width: 746px;
    height: 426px;
  }

  /* Front */
  .card--front { top: 120px; background: var(--card-paper); }
  .brand-block {
    position: absolute;
    left: 0; top: 59px;
    width: 115px; height: 115px;
    background: var(--navy);
  }
  .brand-name {
    position: absolute;
    left: 174px; top: 66px;
    color: var(--navy);
    font-weight: 400;
    line-height: 1.1;
  }
  .brand-name__main { display: block; font-size: 41px; letter-spacing: 2px; }
  .brand-name__sub { display: block; font-size: 29px; letter-spacing: 2.5px; }

  .holder { position: absolute; left: 174px; top: 222px; }
  .holder__name {
    font-size: 27px; font-weight: 700; color: var(--navy);
    letter-spacing: 0.3px; line-height: 1.2;
  }
  .holder__role {
    font-size: 19px; color: var(--sky); letter-spacing: 0.5px; margin-top: 3px;
  }

  .contact { position: absolute; left: 174px; top: 308px; list-style: none; }
  .contact__item {
    display: flex; align-items: center;
    font-size: 19px; color: var(--ink);
    height: 29px;
  }
  .contact__icon { width: 18px; height: 20px; margin-right: 11px; flex: none; }

  /* Back */
  .card--back { top: 637px; background: var(--navy-deep); }
  .back-brand {
    position: absolute;
    right: 44px; top: 270px;
    text-align: right;
    color: var(--pale-text);
    font-weight: 400;
  }
  .back-brand__main { display: block; font-size: 44px; letter-spacing: 4px; line-height: 1.05; }
  .back-brand__sub { display: block; font-size: 30px; letter-spacing: 3px; line-height: 1.2; }
  .back-web {
    position: absolute;
    right: 44px; top: 360px;
    font-size: 19px; color: var(--pale-text);
  }
</style>
</head>
<body>
<main class="canvas">

  <section class="card card--front" aria-label="Business card front">
    <div class="brand-block"></div>
    <div class="brand-name">
      <span class="brand-name__main">AMBER</span>
      <span class="brand-name__sub">Loom systems</span>
    </div>

    <div class="holder">
      <h1 class="holder__name">CLARA FENWICK</h1>
      <p class="holder__role">DIRECTOR</p>
    </div>

    <ul class="contact">
      <li class="contact__item">
        <svg class="contact__icon" viewBox="0 0 18 20" aria-hidden="true">
          <rect x="4" y="1" width="10" height="18" rx="1.6" fill="none" stroke="#0b3664" stroke-width="2"/>
          <line x1="7.5" y1="16" x2="10.5" y2="16" stroke="#0b3664" stroke-width="1.6"/>
        </svg>
        0437 518 902
      </li>
      <li class="contact__item">
        <svg class="contact__icon" viewBox="0 0 18 20" aria-hidden="true">
          <rect x="1" y="5" width="16" height="11" fill="#0b3664"/>
          <polyline points="1.5,5.5 9,11.5 16.5,5.5" fill="none" stroke="#eeeff1" stroke-width="1.4"/>
        </svg>
        clara.fenwick@amberLoomSystems.com.au
      </li>
    </ul>
  </section>

  <section class="card card--back" aria-label="Business card back">
    <div class="back-brand">
      <span class="back-brand__main">AMBER</span>
      <span class="back-brand__sub">Loom systems</span>
    </div>
    <p class="back-web">amberLoomSystems.com.au</p>
  </section>

</main>
</body>
</html>
```